K742 PowerPoint Presentation

As you can see the design of this PowerPoint isn't cohesive. There are a lot of images and words that give it a very jumbled and busy appeal. We want to turn this into a sharp, cohesive and visually appealing presentation without taking away too much of the information. Feel free to use the images to create your own artwork for the PowerPoint.

Please don't hesitate to contact me with any questions.

```html
<!DOCTYPE html>
<html lang="en">
<head>
<meta charset="utf-8">
<title>K742 – Realized Benefits</title>
<link rel="stylesheet" href="https://fonts.googleapis.com/css2?family=Ubuntu:wght@500;700&family=Noto+Sans:wght@400&display=swap">
<style>
  :root {
    --header-deep: #0d4fb8;
    --header-mid: #2a78de;
    --header-light: #8cc0f2;
    --accent-blue: #1565c0;
    --icon-blue: #0e4fa8;
    --body-text: #3a3a3a;
    --footer-navy: #0a2a88;
    --white: #ffffff;
    --photo-light: #e9eef3;
    --photo-mid: #b8c3cf;
    --photo-dark: #4d5a68;
  }
  * { margin: 0; padding: 0; box-sizing: border-box; }
  html, body { width: 1200px; height: 900px; overflow: hidden; background: var(--white); }
  .slide { position: relative; width: 1200px; height: 900px; background: var(--white); overflow: hidden; font-family: "Noto Sans", Arial, sans-serif; }

  .slide-header { position: absolute; inset: 0 0 auto 0; height: 114px; }
  .slide-header svg { position: absolute; inset: 0; }
  .slide-title { position: absolute; left: 45px; top: 36px; font-family: "Ubuntu", Arial, sans-serif; font-weight: 700; font-size: 34px; color: var(--white); letter-spacing: 0.3px; }
  .brand-name { position: absolute; right: 40px; top: 44px; font-family: "Ubuntu", Arial, sans-serif; font-weight: 500; font-size: 24px; color: var(--accent-blue); display: flex; align-items: center; gap: 10px; }
  .brand-dot { width: 14px; height: 14px; border-radius: 50%; background: var(--accent-blue); }

  .benefit-list { position: absolute; left: 44px; top: 184px; width: 680px; list-style: none; }
  .benefit { position: absolute; left: 0; width: 680px; }
  .benefit-icon { position: absolute; left: 0; top: 3px; width: 27px; height: 27px; }
  .benefit-heading { margin-left: 49px; font-family: "Ubuntu", Arial, sans-serif; font-weight: 500; font-size: 26px; line-height: 37px; color: var(--accent-blue); }
  .benefit-detail { margin-left: 49px; margin-top: 10px; font-size: 19.5px; line-height: 31px; color: var(--body-text); }
  .benefit-detail.is-indented { margin-left: 56px; margin-top: 6px; }

  .benefit-1 { top: 0; }
  .benefit-2 { top: 100px; }
  .benefit-3 { top: 284px; }
  .benefit-4 { top: 465px; }

  .photo-frame { position: absolute; left: 759px; top: 190px; width: 399px; height: 603px; background: var(--white); padding: 6px; box-shadow: 0 2px 8px rgba(0,0,0,0.25); }
  .photo-fill { width: 100%; height: 100%; background: radial-gradient(circle at 20% 45%, var(--photo-light) 0%, var(--photo-mid) 60%, var(--photo-dark) 100%); }

  .slide-footer { position: absolute; left: 0; bottom: 0; width: 1200px; height: 40px; background: var(--footer-navy); }
  .footer-note { position: absolute; left: 18px; top: 9px; font-size: 16px; color: var(--white); }
</style>
</head>
<body>
<main class="slide">
  <header class="slide-header">
    <svg width="1200" height="114" viewBox="0 0 1200 114" aria-hidden="true">
      <defs>
        <linearGradient id="headerGradient" x1="0" y1="0" x2="1" y2="0.4">
          <stop offset="0" stop-color="var(--header-deep)"/>
          <stop offset="0.55" stop-color="var(--header-mid)"/>
          <stop offset="1" stop-color="var(--header-light)"/>
        </linearGradient>
      </defs>
      <rect width="1200" height="114" fill="url(#headerGradient)"/>
      <polygon points="930,114 992,10 1200,10 1200,114" fill="var(--white)"/>
      <line x1="922" y1="114" x2="986" y2="6" stroke="var(--header-deep)" stroke-width="3"/>
    </svg>
    <h1 class="slide-title">Realized Benefits</h1>
    <div class="brand-name"><span class="brand-dot"></span>Varden Systems</div>
  </header>

  <ul class="benefit-list">
    <li class="benefit benefit-1">
      <svg class="benefit-icon" viewBox="0 0 27 27" aria-hidden="true"><circle cx="13.5" cy="13.5" r="13.5" fill="var(--icon-blue)"/><polyline points="10.5,7.5 16.5,13.5 10.5,19.5" fill="none" stroke="var(--white)" stroke-width="3.2" stroke-linecap="round" stroke-linejoin="round"/></svg>
      <h2 class="benefit-heading">Identified the need to create a common taxonomy</h2>
      <p class="benefit-detail is-indented">Allowing for simplified data association/collection/display</p>
    </li>
    <li class="benefit benefit-2">
      <svg class="benefit-icon" viewBox="0 0 27 27" aria-hidden="true"><circle cx="13.5" cy="13.5" r="13.5" fill="var(--icon-blue)"/><polyline points="10.5,7.5 16.5,13.5 10.5,19.5" fill="none" stroke="var(--white)" stroke-width="3.2" stroke-linecap="round" stroke-linejoin="round"/></svg>
      <h2 class="benefit-heading">Significantly reduced data call response time for<br>budget and congressional inquiries</h2>
      <p class="benefit-detail">Required data compiled rapidly and accurately responses to<br>data call at all levels of the enterprise</p>
    </li>
    <li class="benefit benefit-3">
      <svg class="benefit-icon" viewBox="0 0 27 27" aria-hidden="true"><circle cx="13.5" cy="13.5" r="13.5" fill="var(--icon-blue)"/><polyline points="10.5,7.5 16.5,13.5 10.5,19.5" fill="none" stroke="var(--white)" stroke-width="3.2" stroke-linecap="round" stroke-linejoin="round"/></svg>
      <h2 class="benefit-heading">Significantly reduced data call response time for<br>budget and congressional inquiries</h2>
      <p class="benefit-detail">Required data compiled rapidly and accurately responses to<br>data call at all levels of the enterprise</p>
    </li>
    <li class="benefit benefit-4">
      <svg class="benefit-icon" viewBox="0 0 27 27" aria-hidden="true"><circle cx="13.5" cy="13.5" r="13.5" fill="var(--icon-blue)"/><polyline points="10.5,7.5 16.5,13.5 10.5,19.5" fill="none" stroke="var(--white)" stroke-width="3.2" stroke-linecap="round" stroke-linejoin="round"/></svg>
      <h2 class="benefit-heading">Provided integrated analysis of live systems,<br>requirements and products data which allowed<br>in-depth analysis of system contributions to<br>functional capabilities</h2>
    </li>
  </ul>

  <figure class="photo-frame">
    <div class="photo-fill" role="img" aria-label="Close-up photograph of a white wall clock face with hands near twelve o'clock"></div>
  </figure>

  <footer class="slide-footer">
    <p class="footer-note">© 2014 K742, All Rights Reserved</p>
  </footer>
</main>
</body>
</html>
```